Plate of the Raven: Half-Page Magazine Ad

advertisement in a travel magazine for a casual/fine dining restaurant in the heart of Whitehorse, Yukon
Needs to say that it is located in the Stonefield Hotel, 247 Larch Avenue.

Northern inspired cuisine
plateoftheraven.example

Don't need to use all the pictures

Dimensions: ad is a half-page, dimensions are 7.25" x 4.8".

Target Market(s)

Upscale dining, corporate travellers

Industry/Entity Type

Restaurant

Colors
0054AA
0677BA
7BADD7
CADEEF
E8F1F8
0094D4
00A9DD
6FCCEA
C7EBF8
E9F6FB
00AB8E
00BBA5
67D7C9
C6EFE9
E9F9F6

Requirements
Must have
• Restaurant logo
Nice to have
• Simple, clean design with upscale feel

```html
<!DOCTYPE html>
<html lang="en">
<head>
<meta charset="utf-8">
<title>Plate of the Raven – Half-Page Ad</title>
<link href="https://fonts.googleapis.com/css2?family=Poppins:wght@300;600;700&display=swap" rel="stylesheet">
<style>
  :root {
    --page: #ffffff;
    --ink: #0d0d0d;
    --heading: #3b3b3b;
    --band-dark: #0a0a0a;
    --band-mid: #262626;
    --muted: #b9b9b9;
    --white: #ffffff;
    --sketch-light: #eeeeee;
    --sketch-mid: #a9a9a9;
    --terrace-light: #b7bcc0;
    --terrace-dark: #3c4146;
    --dish-light: #f0a04b;
    --dish-dark: #b4501c;
    --bowl: #6e6660;
  }
  * { box-sizing: border-box; margin: 0; padding: 0; }
  html, body {
    width: 1200px; height: 900px; overflow: hidden;
    background: var(--page);
    font-family: "Poppins", sans-serif;
  }
  .ad {
    position: absolute; left: 0; top: 52px;
    width: 1200px; height: 795px;
    background: var(--page);
    overflow: hidden;
  }
  .sketch {
    position: absolute; left: 0; top: 0; width: 400px; height: 590px;
    background: radial-gradient(ellipse 60% 55% at 45% 45%, var(--sketch-mid), var(--sketch-light) 70%, var(--page) 100%);
  }
  .contact-band {
    position: absolute; left: 0; top: 582px; width: 1200px; height: 213px;
    background: linear-gradient(90deg, var(--band-mid), var(--band-dark) 60%);
  }
  .wordmark {
    position: absolute; left: 404px; top: 84px; width: 250px;
    font-weight: 700; color: var(--ink); text-transform: uppercase;
    font-size: 66px; line-height: 100px; letter-spacing: 1px;
  }
  .divider {
    position: absolute; left: 680px; top: 81px; width: 1px; height: 312px;
    background: var(--heading);
  }
  .headline {
    position: absolute; left: 712px; top: 76px;
    color: var(--heading); font-size: 54px; text-transform: uppercase;
  }
  .headline strong { display: block; font-weight: 700; line-height: 53px; }
  .headline span { display: block; font-weight: 300; line-height: 55px; }
  .art { position: absolute; left: 0; top: 0; width: 1200px; height: 795px; }
  .badge-text {
    position: absolute; left: 606px; top: 480px; width: 200px;
    text-align: center; color: var(--white); font-weight: 700;
    font-size: 28px; line-height: 30px; text-transform: uppercase;
  }
  .badge-text .soft { color: #cfcfcf; }
  .contact {
    position: absolute; left: 54px; top: 611px; color: var(--white);
  }
  .contact h2 { font-size: 27px; font-weight: 600; color: var(--muted); margin-bottom: 14px; }
  .contact li {
    list-style: none; display: flex; align-items: center; gap: 8px;
    font-size: 19px; font-weight: 600; line-height: 31px;
  }
  .contact svg { width: 18px; height: 18px; fill: none; stroke: var(--muted); stroke-width: 1.8; }
</style>
</head>
<body>
<main class="ad">
  <div class="sketch" role="img" aria-label="Pencil sketch of an animal head in soft grey tones"></div>
  <div class="contact-band"></div>

  <div class="wordmark">Plate<br>of the<br>Raven</div>
  <div class="divider"></div>
  <h1 class="headline">
    <strong>A fine</strong><strong>dining</strong><strong>restaurant</strong>
    <span>in the heart of</span><span>Whitehorse,</span><span>Yukon</span>
  </h1>

  <svg class="art" viewBox="0 0 1200 795" aria-hidden="false">
    <defs>
      <linearGradient id="terrace" x1="0" y1="0" x2="1" y2="1">
        <stop offset="0" stop-color="var(--terrace-light)"/>
        <stop offset="1" stop-color="var(--terrace-dark)"/>
      </linearGradient>
      <radialGradient id="dish" cx="0.4" cy="0.45" r="0.6">
        <stop offset="0" stop-color="var(--dish-light)"/>
        <stop offset="0.8" stop-color="var(--dish-dark)"/>
        <stop offset="1" stop-color="var(--bowl)"/>
      </radialGradient>
      <radialGradient id="badge" cx="0.5" cy="0.3" r="0.7">
        <stop offset="0" stop-color="#3a3a3a"/>
        <stop offset="1" stop-color="#000"/>
      </radialGradient>
    </defs>
    <circle cx="544" cy="602" r="168" fill="#ffffff" fill-opacity="0.12"/>
    <circle cx="544" cy="602" r="148" fill="url(#terrace)" role="img" aria-label="Photo of the restaurant patio with tables and flower baskets"/>
    <circle cx="972" cy="735" r="312" fill="url(#dish)" role="img" aria-label="Photo of a bowl of pasta with ragù, shaved cheese and microgreens"/>
    <circle cx="706" cy="520" r="101" fill="url(#badge)"/>
  </svg>

  <p class="badge-text">Northern<br>Inspired<br><span class="soft">Cuisine</span></p>

  <section class="contact">
    <h2>Contact Us</h2>
    <ul>
      <li><svg viewBox="0 0 24 24"><path d="M5 3h4l2 5-2.5 1.5a11 11 0 0 0 6 6L16 13l5 2v4a2 2 0 0 1-2 2A17 17 0 0 1 3 5a2 2 0 0 1 2-2z"/></svg>867-555-0142</li>
      <li><svg viewBox="0 0 24 24"><rect x="3" y="5" width="18" height="14"/><path d="M3 5l9 8 9-8"/></svg>Stonefield Hotel, 247 Larch Avenue</li>
      <li><svg viewBox="0 0 24 24"><circle cx="12" cy="12" r="9"/><path d="M3 12h18M12 3c3 3 3 15 0 18M12 3c-3 3-3 15 0 18"/></svg>www.plateoftheraven.example</li>
    </ul>
  </section>
</main>
</body>
</html>
```